4D Cradle Glimpse Luxury Ultrasound Billboard

Design a HIGH-END, MODERN billboard for my private prenatal ultrasound studio, 4D Cradle Glimpse, located in Pace, Florida.
This billboard will be viewed by drivers traveling at highway speeds, so it must be extremely clean, simple, and readable within 6 seconds.
About My Business
4D Cradle Glimpse is a private prenatal ultrasound studio specializing in:
Highest technology 4D/HD Ultrasounds
Early Gender Determination
Pregnancy Confirmation
I have been serving families for nearly 10 years and is known for creating a memorable experience, not just an ultrasound appointment.
Design Style
I DO NOT want:
Flowers
Leaves
Swirls
Glitter
Hearts everywhere
Busy backgrounds
Generic maternity stock graphics
I DO want:
Modern
Luxury
Upscale
Clean
Professional
Eye-catching
Premium medical spa feel
Colors
Use colors from my logo:
LOGO Green ( or a deep green)
Black
White
Soft Gold accents
Images:
Incorporate my professional headshot in a clean, modern way, logo, and the ultrasound images
Text
Keep wording minimal.
Primary Headline ( OPEN TO IDEAS) :
EXAMPLES ( WOULD RATHER SOMETHING MORE CATCHY)
" ADVANCED IMAGING. UNFORGETTABLE MOMENTS"
"MEET YOUR BABY BEFORE BIRTH"
Under headline:
4D Ultrasound • Early Gender • Pregnancy Confirmation
Business Name:
4D Cradle Glimpse
Private Prenatal Ultrasound Studio
Phone Number:
850-471-5923
Important
This billboard must be readable in 5–6 seconds from a moving vehicle.
Less text is better.
The phone number and business name must be visible from a distance.
The design should feel like a premium brand that immediately tells expecting parents:
“This is where I go to see my baby.”
Files Provided
Official logo
Headshot
Ultrasound images
Don’t make this look like a medical office billboard.
Make it look like a luxury baby experience billboard. That’s what separates 4D Cradle Glimpse from hospitals, OB offices, and all the new studios popping up around you. The emotional connection is what gets moms to book. ❤️
Billboard Size - 10.6” x 36”

```html
<!DOCTYPE html>
<html lang="en">
<head>
<meta charset="utf-8">
<title>4D Cradle Glimpse Billboard</title>
<link href="https://fonts.googleapis.com/css2?family=Poppins:wght@500;600;700&family=Playfair+Display:wght@700&display=swap" rel="stylesheet">
<style>
  :root {
    --page: #d4d4d4;
    --forest: #2b342e;
    --sage: #55695b;
    --white: #ffffff;
    --gold: #d2a94e;
    --gold-light: #e8c97a;
    --gold-deep: #a87c2c;
    --logo-green: #3e5446;
    --photo-light: #e6e3e0;
    --photo-mid: #9aa79c;
  }
  * { margin: 0; padding: 0; box-sizing: border-box; }
  html, body { width: 1105px; height: 1200px; overflow: hidden; background: var(--page); }
  .billboard {
    position: absolute; left: 32px; top: 340px;
    width: 1040px; height: 520px;
    background: var(--forest);
    overflow: hidden;
    font-family: "Poppins", sans-serif;
    color: var(--white);
  }
  .services-band { position: absolute; left: 0; top: 332px; width: 764px; height: 105px; background: var(--sage); }
  .footer-band { position: absolute; left: 0; top: 437px; width: 1040px; height: 83px; background: var(--forest); }
  .gold-rule { position: absolute; left: 757px; top: 0; width: 7px; height: 437px;
    background: linear-gradient(180deg, var(--gold-light), var(--gold-deep)); }
  .headshot { position: absolute; left: 764px; top: 0; width: 276px; height: 437px;
    background: linear-gradient(160deg, var(--photo-light) 0%, #cfcac4 45%, var(--photo-mid) 75%, var(--logo-green) 100%); }
  .logo-box { position: absolute; left: 311px; top: 22px; width: 155px; height: 88px;
    background: var(--white); display: flex; align-items: center; justify-content: center;
    text-align: center; }
  .logo-box .brand-name { font-weight: 600; font-size: 19px; line-height: 1.15; color: var(--logo-green); }
  .headline { position: absolute; left: 0; top: 0; width: 757px; height: 320px; text-align: center; font-weight: 700; }
  .headline span { display: block; white-space: nowrap; }
  .headline .lead { position: absolute; left: 0; right: 0; top: 128px;
    font-weight: 700; font-size: 58px; line-height: 1; letter-spacing: 0.5px; }
  .headline .accent { position: absolute; left: 0; right: 0;
    font-family: "Playfair Display", serif; font-weight: 700; font-size: 70px; line-height: 1;
    letter-spacing: 1px; color: var(--gold);
    background: linear-gradient(90deg, var(--gold-deep), var(--gold-light) 45%, var(--gold) 70%, var(--gold-deep));
    -webkit-background-clip: text; background-clip: text; -webkit-text-fill-color: transparent; }
  .headline .line-one { top: 177px; }
  .headline .line-two { top: 239px; }
  .scan-photo { position: absolute; left: 22px; top: 332px; width: 182px; height: 186px;
    border: 2px solid var(--white);
    background: radial-gradient(circle at 30% 45%, #c98a72, #8e4a38 55%, #3a1810 100%); }
  .service { position: absolute; display: flex; align-items: center; gap: 12px;
    font-weight: 600; font-size: 19px; letter-spacing: 0.5px; line-height: 1.15; white-space: nowrap; }
  .service svg { flex: none; }
  .svc-ultra { left: 236px; top: 349px; }
  .svc-gender { left: 236px; top: 392px; }
  .svc-confirm { left: 500px; top: 353px; align-items: flex-start; gap: 14px; }
  .svc-confirm svg { margin-top: 1px; }
  .svc-divider { position: absolute; left: 471px; top: 358px; width: 1px; height: 62px; background: var(--white); opacity: .8; }
  .phone { position: absolute; left: 242px; top: 450px; width: 446px; text-align: center;
    font-weight: 700; font-size: 56px; line-height: 1; letter-spacing: 2px; white-space: nowrap; }
  .foot-divider { position: absolute; left: 727px; top: 457px; width: 1px; height: 44px; background: var(--white); opacity: .8; }
  .tenure { position: absolute; left: 778px; top: 448px; white-space: nowrap; }
  .tenure .small { font-weight: 600; font-size: 14.4px; line-height: 1; }
  .tenure .big { font-weight: 700; font-size: 49px; line-height: 1; margin-top: 3px; color: var(--gold); }
</style>
</head>
<body>
  <main class="billboard">
    <div class="services-band"></div>
    <div class="footer-band"></div>

    <div class="headshot" role="img" aria-label="Portrait of the studio owner in green scrubs holding an ultrasound probe beside an ultrasound machine"></div>
    <div class="gold-rule"></div>

    <div class="logo-box"><div class="brand-name">4D<br>Cradle Glimpse</div></div>

    <h1 class="headline">
      <span class="lead">ADVANCED IMAGING</span>
      <span class="accent line-one">UNFORGETTABLE</span>
      <span class="accent line-two">MOMENTS</span>
    </h1>

    <div class="scan-photo" role="img" aria-label="4D ultrasound image of twin babies face to face"></div>

    <div class="service svc-ultra">
      <svg width="28" height="30" viewBox="0 0 28 30" fill="none" stroke="#fff" stroke-width="1.4">
        <path d="M8 11h12l-2 9h-8z"/><path d="M12 20v4a2 2 0 0 0 4 0v-4"/>
        <path d="M9 7a8 8 0 0 1 10 0"/><path d="M6 4a12 12 0 0 1 16 0"/>
      </svg>
      <span>4D ULTRASOUND</span>
    </div>
    <div class="service svc-gender">
      <svg width="28" height="28" viewBox="0 0 28 28" fill="none" stroke="#fff" stroke-width="1.6">
        <circle cx="11" cy="14" r="6"/><path d="M11 20v6M8 23h6M15.5 9.5L22 3M17 3h5v5"/>
      </svg>
      <span>EARLY GENDER</span>
    </div>
    <div class="svc-divider"></div>
    <div class="service svc-confirm">
      <svg width="22" height="20" viewBox="0 0 22 20" fill="none" stroke="#fff" stroke-width="3.5" stroke-linecap="round" stroke-linejoin="round">
        <path d="M3 10l5 5L19 4"/>
      </svg>
      <span>PREGNANCY<br>CONFIRMATION</span>
    </div>

    <div class="phone">850-471-5923</div>
    <div class="foot-divider"></div>
    <div class="tenure">
      <div class="small">SERVING FAMILIES FOR NEARLY</div>
      <div class="big">10 YEARS</div>
    </div>
  </main>
</body>
</html>
```